900mm double sided Card Ponytail Insert for hair

I need print ready file designs for card packaging inserts for my line of ponytails, These are two sided colour and fold at each end or contain the hair, for structure and so the brand is on display. These will be marketed as luxury ponytails, so we want a simple, soft but luxurious design feel. All the details are below but it will be the logo, photos and simple messaging

Target Market(s)

18-30 females

Industry/Entity Type

Beauty

Font styles to use
Serif

Requirements
Must have
• - Velmora Logo on the back and top front fold.
'Luxury Synthetic Ponytails' Head line
'For effortlessly long and luxurious hair' tag line
'For tutorials, questions and inspiration head to our 'Glow Corner' on velmorabeauty.com'
www.velmorabeauty.com
Tag us on socials! @velmorabeautyofficial (instagram and Facebook logos)
3 step-by-step pictures (holding pictures please until i have some taken)
Nice to have
• (notes to designers) view our website to see our branding velmorabeauty.com - it would be good to use our brand colours and somekind of tropical leaves maybe? i'm thinking palm leaves?
- my brand font is Sweet Getaway - but this may only be good for the biggest headings

```html
<!DOCTYPE html>
<html lang="en">
<head>
<meta charset="utf-8">
<title>Velmora Beauty – Ponytail Insert</title>
<link rel="stylesheet" href="https://fonts.googleapis.com/css2?family=Questrial&family=Montserrat:wght@500;700&display=swap">
<style>
  :root{
    --canvas:#e4e4e7;
    --gold:#dfa23c;
    --gold-deep:#d08a22;
    --sun:#e9b13a;
    --ink:#232323;
    --paper:#fbfbfa;
    --paper-cool:#ececec;
    --text:#3a3a3a;
    --photo-wood:#8a7a66;
    --photo-hair:#5b4128;
    --photo-portrait:#b9aaa4;
    --photo-scalp:#6a4c3a;
  }
  *{box-sizing:border-box;margin:0;padding:0}
  html,body{width:1200px;height:838px;overflow:hidden;background:var(--canvas)}
  body{position:relative;font-family:"Questrial",sans-serif;color:var(--text)}
  .spread{position:absolute;top:217px;width:572px;height:404px;display:flex;box-shadow:0 14px 30px rgba(0,0,0,.18)}
  .spread--outside{left:16px}
  .spread--inside{left:612px}
  .page{position:relative;width:286px;height:404px;overflow:hidden}
  .page + .page{border-left:1px solid rgba(0,0,0,.06)}

  /* shared */
  .brand{display:flex;align-items:center;gap:8px}
  .brand__dot{width:34px;height:34px;border-radius:50%;background:var(--paper)}
  .brand__name{font-family:"Questrial",sans-serif;letter-spacing:.06em;text-transform:lowercase}
  .photo{position:absolute}

  /* back cover */
  .back{background:var(--paper-cool)}
  .back__band{position:absolute;left:0;top:0;width:286px;height:104px;background:var(--gold);display:flex;align-items:center;padding-left:22px}
  .back__band .brand__dot{width:62px;height:62px}
  .back__band .brand__name{font-size:34px;color:var(--paper)}
  .steps{position:absolute;left:38px;top:128px;width:210px;height:130px;border-radius:34px;overflow:hidden;display:grid;grid-template-columns:1fr 1fr;grid-template-rows:1fr 1fr;gap:4px;background:var(--paper-cool)}
  .steps__photo{background:linear-gradient(160deg,var(--photo-wood),var(--photo-hair) 60%,#caa58a)}
  .back__contact{position:absolute;left:0;top:282px;width:286px;height:122px;background:var(--ink);padding:34px 0 0 26px}
  .contact__line{display:flex;align-items:center;gap:8px;color:var(--gold);font-size:10.5px;line-height:16px;letter-spacing:.02em}
  .contact__line::before{content:"";width:9px;height:1px;background:var(--gold)}

  /* front cover */
  .front{background:var(--paper)}
  .front__intro{position:absolute;left:0;top:0;width:236px;height:150px;display:flex;flex-direction:column;align-items:center;padding-top:28px}
  .front__intro .brand__dot{width:22px;height:22px;background:var(--gold)}
  .front__intro .brand__name{font-size:22px;color:var(--gold)}
  .front__rule{width:70px;height:1px;background:#777;margin:10px 0 12px}
  .tagline{font-size:15px;line-height:17px;text-align:center;color:var(--text)}
  .front__side{position:absolute;right:0;top:22px;width:50px;height:150px;background:var(--gold);display:flex;align-items:center;justify-content:center}
  .vertical{writing-mode:vertical-rl;transform:rotate(180deg);font-size:17px;line-height:17px;letter-spacing:.14em;text-align:center}
  .front__side .vertical{color:var(--text)}
  .front__hero{left:0;top:172px;width:286px;height:92px;background:linear-gradient(100deg,#6f7986 0%,var(--photo-wood) 30%,var(--photo-hair) 70%,#7d6a58 100%)}
  .front__badge{position:absolute;left:0;top:264px;width:50px;height:140px;background:var(--ink);display:flex;align-items:center;justify-content:center}
  .front__badge .vertical{color:var(--paper);font-size:15px;letter-spacing:.06em}
  .headline{position:absolute;left:68px;top:298px;font-family:"Montserrat",sans-serif;font-weight:700;color:var(--gold);font-size:17px;line-height:21px;letter-spacing:.05em}
  .headline__rule{position:absolute;left:168px;top:338px;width:96px;height:1px;background:var(--gold)}

  /* inside left */
  .guide{background:var(--sun);color:var(--paper)}
  .guide__frame-v{position:absolute;left:18px;top:0;width:1px;height:404px;background:rgba(255,255,255,.8)}
  .guide__frame-h{position:absolute;left:0;top:30px;width:286px;height:1px;background:rgba(255,255,255,.8)}
  .guide__text{position:absolute;left:30px;top:14px;width:240px}
  .guide__lead{font-size:10.5px;line-height:14px}
  .guide__title{font-family:"Montserrat",sans-serif;font-weight:700;font-size:22px;line-height:24px;letter-spacing:.01em;color:var(--ink);text-transform:uppercase;margin-top:2px}
  .guide__url{font-size:12px;margin-top:-1px}
  .guide__sub{font-family:"Montserrat",sans-serif;font-weight:700;font-size:8.5px;color:var(--ink);margin-top:12px}
  .guide__body{font-size:8px;line-height:12px;margin-top:6px}
  .guide__portrait{left:44px;top:258px;width:104px;height:128px;background:linear-gradient(170deg,#8b6f66,var(--photo-portrait) 45%,#d8d2d0)}
  .guide__scalp{left:154px;top:258px;width:96px;height:128px;background:linear-gradient(160deg,#1d1816,var(--photo-scalp) 60%,#a98a78)}

  /* inside right */
  .glossary{background:var(--paper-cool);padding:56px 22px 0 30px}
  .entry + .entry{margin-top:34px}
  .entry__title{font-family:"Montserrat",sans-serif;font-weight:700;font-size:10.5px;color:var(--gold-deep);margin-bottom:6px}
  .entry__body{font-size:8.5px;line-height:13px;text-align:justify;color:var(--text)}
</style>
</head>
<body>

<section class="spread spread--outside" aria-label="Outside of insert">
  <article class="page back">
    <header class="back__band">
      <div class="brand"><span class="brand__dot"></span><span class="brand__name">velmora</span></div>
    </header>
    <div class="steps">
      <div class="steps__photo" role="img" aria-label="Step one: ponytail laid out on wood"></div>
      <div class="steps__photo" role="img" aria-label="Step two: ponytail clip close-up"></div>
      <div class="steps__photo" role="img" aria-label="Step three: ponytail attached"></div>
      <div class="steps__photo" role="img" aria-label="Step four: finished ponytail"></div>
    </div>
    <footer class="back__contact">
      <p class="contact__line">www.velmorabeauty.com</p>
      <p class="contact__line">@velmorabeautyofficial</p>
      <p class="contact__line">@velmorabeautyofficial</p>
    </footer>
  </article>

  <article class="page front">
    <div class="front__intro">
      <div class="brand"><span class="brand__dot"></span><span class="brand__name">velmora</span></div>
      <span class="front__rule"></span>
      <p class="tagline">For effortlessly long<br>&amp; luxurious hair</p>
    </div>
    <div class="front__side"><span class="vertical">Velmora<br>Beaut</span></div>
    <div class="photo front__hero" role="img" aria-label="Long brown synthetic ponytail on a wooden surface"></div>
    <div class="front__badge"><span class="vertical">Velmora<br>Beaut</span></div>
    <h1 class="headline">Luxury Synthetic<br>Ponytails</h1>
    <span class="headline__rule"></span>
  </article>
</section>

<section class="spread spread--inside" aria-label="Inside of insert">
  <article class="page guide">
    <span class="guide__frame-v"></span>
    <span class="guide__frame-h"></span>
    <div class="guide__text">
      <p class="guide__lead">For Tutorials,<br>questions and inspiration head to our</p>
      <h2 class="guide__title">Glow Corner</h2>
      <p class="guide__url">on velmorabeauty.com</p>
      <p class="guide__sub">A guide to wearing a wig with alopecia - A Guest Blog.</p>
      <p class="guide__body">In recent months we have stocked wigs that are synthetic but are not lace front wigs, you may have noticed them because of the price difference listed on our site. So what's the difference and should you purchase one? What is a lace front wig? A wig's called lace front...</p>
    </div>
    <div class="photo guide__portrait" role="img" aria-label="Woman wearing a long ombré wig"></div>
    <div class="photo guide__scalp" role="img" aria-label="Close-up of a lace front hairline"></div>
  </article>

  <article class="page glossary">
    <div class="entry">
      <h3 class="entry__title">Wig Glossary - Wig Terms &amp; Words Explained</h3>
      <p class="entry__body">Our simple glossary breaks down the jargon of wig language. If you've seen terms or words that you are unsure of when looking at our wigs, we've made this guide for you</p>
    </div>
    <div class="entry">
      <h3 class="entry__title">Wig Glossary - Wig Terms &amp; Words Explained</h3>
      <p class="entry__body">Our simple glossary breaks down the jargon of wig language. If you've seen terms or words that you are unsure of when looking at our wigs, we've made this guide for you</p>
    </div>
    <div class="entry">
      <h3 class="entry__title">Wig Glossary - Wig Terms &amp; Words Explained</h3>
      <p class="entry__body">Our simple glossary breaks down the jargon of wig language. If you've seen terms or words that you are unsure of when looking at our wigs, we've made this guide for you</p>
    </div>
  </article>
</section>

</body>
</html>
```